Marlowe Crest Realty business card design

Looking for an upscale and clean business card design and updated logo. I sell to a very high-end south Florida real estate market.
Target Market(s)
High-end real estate in south Florida real estate market
Industry/Entity Type
Real Estate Agent
Contact Information for Business Card
Marlowe Crest Realty, Inc
738 West Pinecrest Ave, Suite 410/510, Fort Lauderdale, FL 33308
Gary Whitlock - Broker/Owner
954-327-8846 Direct
garyshomes@quellmail.com
Website: DwellTarrowBay.com
Font styles to use
Other font styles liked:
- Copperplate Gothic, Georgia, etc.
Requirements
Must have
- My photo, company name, my name and title, all info stated in Details above
Nice to have
- Luxury home design element, waterfront

```html
<!DOCTYPE html>
<html lang="en">
<head>
<meta charset="utf-8">
<title>Marlowe Crest Realty – Business Card</title>
<link href="https://fonts.googleapis.com/css2?family=Cinzel:wght@700&family=Montserrat:wght@400;500&display=swap" rel="stylesheet">
<style>
  :root {
    --page: #e9e9e9;
    --card-black: #141416;
    --card-black-2: #1e1e21;
    --gold: #f3c21b;
    --gold-deep: #c99a12;
    --white: #ffffff;
    --muted: #e6e6e6;
    --photo-light: #e8ebee;
    --photo-blue: #2f4f9a;
  }
  * { margin: 0; padding: 0; box-sizing: border-box; }
  html, body { width: 1200px; height: 900px; overflow: hidden; }
  body {
    background: var(--page);
    font-family: "Montserrat", Arial, sans-serif;
    position: relative;
  }
  .card {
    position: absolute;
    left: 250px;
    width: 700px;
    height: 400px;
    border-radius: 22px;
    overflow: hidden;
    background: var(--card-black);
  }
  .card--back { top: 40px; }
  .card--front { top: 465px; }

  /* back side */
  .back-pattern {
    position: absolute; inset: 0;
    background: radial-gradient(ellipse at 15% 80%, #3a3a3d 0%, var(--card-black-2) 45%, var(--card-black) 100%);
  }
  .back-brand {
    position: absolute;
    right: 90px; top: 150px;
    display: flex; align-items: center; gap: 12px;
  }
  .brand-dot {
    width: 34px; height: 34px; border-radius: 50%;
    background: var(--gold);
  }
  .brand-name {
    font-family: "Montserrat", Arial, sans-serif;
    font-weight: 500;
    font-size: 15px;
    color: var(--gold);
    letter-spacing: 0.3px;
  }

  /* front side */
  .front-photo {
    position: absolute; inset: 0;
    clip-path: polygon(55% 0, 100% 0, 100% 100%, 67% 100%);
    background: linear-gradient(160deg, var(--photo-light) 0%, #d6dadf 45%, var(--photo-blue) 100%);
  }
  .front-stripe {
    position: absolute; inset: 0;
    background: var(--gold);
    clip-path: polygon(52.6% 0, 53.6% 0, 66% 100%, 65% 100%);
  }
  .front-logo {
    position: absolute; left: 38px; top: 36px;
    display: flex; align-items: center; gap: 12px;
  }
  .front-logo .brand-dot { width: 40px; height: 40px; }
  .front-logo .brand-name { color: var(--white); font-size: 15px; }

  .name-band {
    position: absolute; left: 0; top: 128px;
    width: 470px; height: 58px;
    background: linear-gradient(90deg, var(--gold) 0%, var(--gold-deep) 30%, rgba(120,95,40,0.55) 65%, rgba(20,20,22,0) 100%);
  }
  .agent-name {
    position: absolute; left: 40px; top: 132px;
    font-family: "Cinzel", Georgia, serif;
    font-weight: 700; font-size: 30px;
    color: var(--white); letter-spacing: 2px;
  }
  .agent-title {
    position: absolute; left: 40px; top: 172px;
    font-size: 17px; color: var(--muted);
  }
  .details {
    position: absolute; left: 40px; top: 210px;
    font-size: 15px; line-height: 21px; color: var(--white);
  }
  .details .company { color: var(--gold); }
  .contacts {
    position: absolute; left: 40px; top: 300px;
    list-style: none;
    font-size: 15px; line-height: 24px; color: var(--white);
  }
  .contacts li { display: flex; align-items: center; gap: 10px; }
  .contacts svg { width: 14px; height: 14px; fill: var(--gold); flex: none; }
  .contacts .accent { color: var(--gold); }
</style>
</head>
<body>

<section class="card card--back" aria-label="Card back">
  <div class="back-pattern" role="img" aria-label="Dark embossed repeating brand pattern"></div>
  <div class="back-brand">
    <span class="brand-dot"></span>
    <span class="brand-name">Marlowe Crest Realty</span>
  </div>
</section>

<section class="card card--front" aria-label="Card front">
  <div class="front-photo" role="img" aria-label="Portrait photo of the broker in a blue blazer"></div>
  <div class="front-stripe"></div>

  <div class="front-logo">
    <span class="brand-dot"></span>
    <span class="brand-name">Marlowe Crest Realty, Inc.</span>
  </div>

  <div class="name-band"></div>
  <h1 class="agent-name">GARY WHITLOCK</h1>
  <p class="agent-title">Broker/Owner</p>

  <address class="details" style="font-style:normal">
    <span class="company">Marlowe Crest Realty, Inc</span><br>
    738 West Pinecrest Ave,<br>
    Suite 410/510,<br>
    Fort Lauderdale, FL 33308
  </address>

  <ul class="contacts">
    <li>
      <svg viewBox="0 0 24 24" aria-hidden="true"><path d="M6.6 10.8a15.1 15.1 0 0 0 6.6 6.6l2.2-2.2c.3-.3.7-.4 1-.2 1.1.4 2.3.6 3.6.6.6 0 1 .4 1 1V20c0 .6-.4 1-1 1A17 17 0 0 1 3 4c0-.6.4-1 1-1h3.5c.6 0 1 .4 1 1 0 1.3.2 2.5.6 3.6.1.3 0 .7-.2 1z"/></svg>
      954-327-8846
    </li>
    <li>
      <svg viewBox="0 0 24 24" aria-hidden="true"><path d="M2 5h20v14H2zm2 2v.5l8 5 8-5V7l-8 5z"/></svg>
      garyshomes@quellmail.com
    </li>
    <li>
      <svg viewBox="0 0 24 24" aria-hidden="true"><circle cx="12" cy="12" r="10"/></svg>
      <span>www.<span class="accent">DwellTarrowBay</span>.com</span>
    </li>
  </ul>
</section>

</body>
</html>
```